RK Donnelly & Associates

Create a website encompassing design work already carried out for business card.
Small accounting practice, business accounting and management, superannuation, audit, taxation.

```html
<!DOCTYPE html>
<html lang="en">
<head>
<meta charset="utf-8">
<title>RK Donnelly &amp; Associates</title>
<link rel="stylesheet" href="https://fonts.googleapis.com/css2?family=Open+Sans:wght@400;600&family=Signika:wght@400;600&display=swap">
<style>
:root{
  --dark:#1c1c1c;
  --blue:#6ea8de;
  --blue-ring:#d7e6f4;
  --text:#7a7a7a;
  --heading:#3a3a3a;
  --rule:#dedede;
  --white:#ffffff;
}
*{margin:0;padding:0;box-sizing:border-box}
html,body{width:962px;height:1200px;overflow:hidden;background:var(--white)}
body{position:relative;font-family:Arial,Helvetica,sans-serif;color:var(--text)}
.abs{position:absolute}
.site-header{left:0;top:0;width:962px;height:114px;background:var(--dark)}
.brand{left:105px;top:20px;display:flex;align-items:center;gap:8px;color:var(--white);font-family:'Signika',sans-serif;font-weight:600;font-size:16px;line-height:1.05}
.brand-mark{width:22px;height:22px;background:var(--blue)}
.main-nav{right:105px;top:42px;display:flex;gap:22px;font-size:10px;color:var(--white);text-transform:uppercase}
.main-nav .active{color:var(--blue)}
.tagline{left:105px;top:72px;width:752px;height:42px;background:var(--blue);color:var(--white);font-weight:bold;font-size:10px;padding:15px 0 0 6px}
.hero{left:105px;top:114px;width:752px;height:353px;background:linear-gradient(180deg,#c9d6e2 0%,#aebdcc 45%,#8f9fb2 100%)}
.hero-caption{left:105px;top:426px;width:752px;height:41px;background:rgba(40,40,40,.72)}
.hero-title{left:126px;top:437px;color:var(--white);font-family:'Signika',sans-serif;font-size:16px}
.hero-arrow{top:436px;width:26px;height:26px;border:2px solid #bbb;border-radius:50%}
.service{top:502px;width:140px;text-align:center}
.service-icon{display:block;margin:0 auto;width:96px;height:96px;border-radius:50%;background:var(--blue);border:4px solid var(--blue-ring)}
.service h3{margin-top:18px;font-family:'Signika',sans-serif;font-weight:400;font-size:11.5px;color:var(--heading);text-transform:uppercase}
.service p{margin-top:9px;font-size:9px;line-height:16px}
.rule{height:1px;background:var(--rule)}
.section-title{font-family:'Signika',sans-serif;font-size:14px;color:var(--heading);font-weight:400}
.section-title span{color:var(--blue)}
.welcome-photo{left:105px;top:742px;width:196px;height:167px;background:linear-gradient(135deg,#e9eef2,#b8c3cc 60%,#8e99a4)}
.welcome-body{left:319px;top:744px;width:268px}
.welcome-body h4{font-family:'Signika',sans-serif;font-weight:400;font-size:10.5px;color:var(--blue);margin-bottom:12px}
.welcome-body p{font-size:9px;line-height:16.5px;margin-bottom:12px}
.welcome-body a{color:var(--blue);text-decoration:none}
.news-item{left:610px;width:248px}
.news-date{position:absolute;left:0;top:0;width:28px;height:28px;background:#2b2b2b;color:var(--white);font-size:9px;text-align:center;line-height:11px;padding-top:3px}
.news-title{margin-left:38px;font-family:'Signika',sans-serif;font-size:10px;line-height:15px;color:var(--heading)}
.news-excerpt{margin-top:12px;font-size:8.5px;line-height:17px}
.subscribe{left:117px;top:946px;width:728px;height:77px;border:2px solid #e4e4e4}
.quote-mark{left:132px;top:955px;font-family:Georgia,serif;font-size:56px;color:#bcbcbc;line-height:1}
.quote-text{left:178px;top:969px;width:345px;font-style:italic;font-size:9px;line-height:16.5px}
.v-rule{left:535px;top:958px;width:1px;height:52px;background:var(--rule)}
.email{left:547px;top:971px;width:190px;height:26px;border:1px solid #d4d4d4;font-style:italic;font-size:9px;color:#aaa;padding:8px 0 0 8px}
.subscribe-btn{left:749px;top:971px;width:85px;height:26px;background:var(--blue);border:1px solid #5b95cc;color:var(--white);font-size:9.5px;text-align:center;line-height:24px}
.site-footer{left:0;top:1041px;width:962px;height:159px;background:var(--dark)}
.social{top:1067px;width:30px;height:30px;border-radius:50%;background:var(--white)}
.footer-rule{left:105px;top:1114px;width:752px;height:1px;background:#444}
.footer-nav{left:0;top:1128px;width:962px;display:flex;justify-content:center;gap:18px;color:var(--white);font-size:9.5px}
.footer-nav .sep{color:#ccc}
.copyright{left:0;top:1160px;width:962px;text-align:center;color:var(--white);font-size:9px}
</style>
</head>
<body>

<header class="abs site-header"></header>
<div class="abs brand"><span class="brand-mark"></span><span>RK Donnelly<br>&amp; Associates</span></div>
<nav class="abs main-nav">
  <span class="active">Home</span><span>About Us</span><span>Services</span><span>News</span><span>Testimonials</span><span>Contact Us</span>
</nav>
<div class="abs tagline">Accountant · Business Solutions · Management · Superannuation · Audit</div>

<div class="abs hero" role="img" aria-label="Photo of a smiling team of five young professionals in light blue shirts"></div>
<div class="abs hero-caption"></div>
<div class="abs hero-title">NEQUE PORRO QUISQUAM EST QUI DOLOREM</div>
<div class="abs hero-arrow" style="left:793px">
  <svg width="22" height="22" viewBox="0 0 22 22"><path d="M13 6 L8 11 L13 16" fill="none" stroke="#ccc" stroke-width="2"/></svg>
</div>
<div class="abs hero-arrow" style="left:825px">
  <svg width="22" height="22" viewBox="0 0 22 22"><path d="M9 6 L14 11 L9 16" fill="none" stroke="#ccc" stroke-width="2"/></svg>
</div>

<section class="abs service" style="left:108px">
  <svg class="service-icon" viewBox="0 0 96 96"><rect width="96" height="96" fill="none"/>
    <path d="M40 26h16l-4 8h-8z" fill="#fff"/><path d="M44 36h8c12 8 16 20 16 28 0 6-4 8-20 8s-20-2-20-8c0-8 4-20 16-28z" fill="#fff"/>
    <text x="48" y="63" text-anchor="middle" font-family="Arial" font-weight="bold" font-size="20" fill="#6ea8de">$</text></svg>
  <h3>Accounting</h3><p>Sed ut perspiciatis unde omnis sunt explicabo.</p>
</section>
<section class="abs service" style="left:260px">
  <svg class="service-icon" viewBox="0 0 96 96">
    <rect x="24" y="58" width="7" height="14" fill="#fff"/><rect x="34" y="52" width="7" height="20" fill="#fff"/><rect x="44" y="46" width="7" height="26" fill="#fff"/><rect x="54" y="40" width="7" height="32" fill="#fff"/><rect x="64" y="34" width="7" height="38" fill="#fff"/>
    <path d="M24 50 L50 32 L60 36 L72 24" fill="none" stroke="#fff" stroke-width="3"/><path d="M66 22h8v8" fill="none" stroke="#fff" stroke-width="3"/>
    <text x="34" y="38" text-anchor="middle" font-family="Arial" font-weight="bold" font-size="18" fill="#fff">$</text></svg>
  <h3>Business Accounting</h3><p>Sed ut perspiciatis unde omnis sunt explicabo.</p>
</section>
<section class="abs service" style="left:413px">
  <svg class="service-icon" viewBox="0 0 96 96">
    <path d="M18 40 L28 30 L34 36 L24 46z M78 40 L68 30 L62 36 L72 46z" fill="#fff"/>
    <path d="M32 40 L46 32 L56 34 L66 42 L56 60 L46 64 L36 56z" fill="#fff"/>
    <path d="M44 42 L52 38" stroke="#6ea8de" stroke-width="2"/></svg>
  <h3>Management</h3><p>Sed ut perspiciatis unde omnis sunt explicabo.</p>
</section>
<section class="abs service" style="left:565px">
  <svg class="service-icon" viewBox="0 0 96 96">
    <path d="M28 34h12a6 6 0 1 1 12 0h12v12a6 6 0 1 1 0 12v12h-12a6 6 0 1 0-12 0h-12z" fill="#fff"/></svg>
  <h3>Superannuation</h3><p>Sed ut perspiciatis unde omnis sunt explicabo.</p>
</section>
<section class="abs service" style="left:715px">
  <svg class="service-icon" viewBox="0 0 96 96">
    <rect x="30" y="24" width="36" height="48" rx="3" fill="none" stroke="#fff" stroke-width="4"/><rect x="40" y="20" width="16" height="7" fill="#fff"/>
    <path d="M36 38l3 3 4-5M36 48l3 3 4-5M36 58l3 3 4-5" fill="none" stroke="#fff" stroke-width="2"/>
    <path d="M47 39h13M47 49h13M47 59h13" stroke="#fff" stroke-width="3"/></svg>
  <h3>Audit</h3><p>Sed ut perspiciatis unde omnis sunt explicabo.</p>
</section>

<div class="abs rule" style="left:105px;top:685px;width:752px"></div>

<h2 class="abs section-title" style="left:105px;top:703px">WELCOME TO <span>RK DONNELLY &amp; ASSOCIATES</span></h2>
<div class="abs welcome-photo" role="img" aria-label="Photo of colleagues meeting around a bright office table"></div>
<article class="abs welcome-body">
  <h4>NEQUE PORRO QUISQUAM EST QUI DOLOREM</h4>
  <p>Sed ut perspiciatis unde omnis iste natus error sit voluptatem accusantium doloremque laudantium, totam rem aperiam, eaque ipsa quae ab illo inventore veritatis et quasi architecto beatae vitae dicta sunt explicabo.</p>
  <p>Perspiciatis unde omnis iste natus error sit voluptatem dicta sunt explicabo.accusantium doloremque laudantium, totam rem aperiam, eaque ipsa quae ab illo inventore veritatis et quasi archi-tecto beatae vitae.......... <a href="#">READ MORE</a></p>
</article>

<h2 class="abs section-title" style="left:609px;top:703px">LATEST <span>NEWS</span></h2>
<article class="abs news-item" style="top:740px">
  <div class="news-date">24<br>Jun</div>
  <p class="news-title">Neque porro quisquam est qui dolorem ipsum quia dolor sit amet, consectetur....</p>
  <p class="news-excerpt">Sed ut perspiciatis unde omnis iste natus error sit voluptatem accusantium doloremque laudantium.........</p>
</article>
<div class="abs rule" style="left:610px;top:821px;width:247px"></div>
<article class="abs news-item" style="top:834px">
  <div class="news-date">24<br>Jun</div>
  <p class="news-title">Neque porro quisquam est qui dolorem ipsum quia dolor sit amet, consectetur....</p>
  <p class="news-excerpt">Sed ut perspiciatis unde omnis iste natus error sit voluptatem accusantium doloremque laudantium.........</p>
</article>

<div class="abs rule" style="left:105px;top:930px;width:752px"></div>

<div class="abs subscribe"></div>
<div class="abs quote-mark">&ldquo;</div>
<p class="abs quote-text">Sed ut perspiciatis unde omnis iste natus error sit voluptatem accusantium doloquasi architecto beatae vitae dicta sunt explicabo.</p>
<div class="abs v-rule"></div>
<div class="abs email">Enter Your Email Address :</div>
<div class="abs subscribe-btn">SUBSCRIBE</div>

<footer class="abs site-footer"></footer>
<span class="abs social" style="left:352px" aria-label="Social link"></span>
<span class="abs social" style="left:390px" aria-label="Social link"></span>
<span class="abs social" style="left:427px" aria-label="Social link"></span>
<span class="abs social" style="left:465px" aria-label="Social link"></span>
<span class="abs social" style="left:503px" aria-label="Social link"></span>
<span class="abs social" style="left:540px" aria-label="Social link"></span>
<span class="abs social" style="left:578px" aria-label="Social link"></span>
<div class="abs footer-rule"></div>
<nav class="abs footer-nav">
  <span>Home</span><span class="sep">|</span><span>About Us</span><span class="sep">|</span><span>Services</span><span class="sep">|</span><span>News</span><span class="sep">|</span><span>Testimonials</span><span class="sep">|</span><span>Contact Us</span>
</nav>
<p class="abs copyright">© Copy Rights 2014 RK Donnelly &amp; Associates.All Rights Reserved</p>

</body>
</html>
```